VORTEQ

It’s is a startup business. We design and build new products.

Target Market(s)

For my first two products, they are targeting the laundry market, hanger accessory, and new modern style clothes dryer. I also have a Pet Treat product at patent stage, and there are other products not yet started but will be more engineering based. Therefore from young adults to older population

Industry/Entity Type

Colours of website to match the logo (att)

Coding

Coded - Design and coding required

Number of Pages Required

1 page

Font styles to use
Other font styles liked:
• Some of the same font as the logo

Colors

Designer to choose colors to be used in the design.

Requirements
Must have
• An upbeat vibe - the logo looks great so inline with that !
Should not have
• anything old fashioned and old style fonts

```html
<!DOCTYPE html>
<html lang="en">
<head>
<meta charset="utf-8">
<title>VORTEQ – Innovation &amp; Technical Services</title>
<link rel="stylesheet" href="https://fonts.googleapis.com/css2?family=Michroma&family=Lato:wght@400;700&display=swap">
<style>
:root{
  --cyan:#1b9cc8;
  --navy:#1f2a72;
  --ink:#2a2a2a;
  --muted:#4a4a4a;
  --title-blue:#2a3a9a;
  --field:#ebebeb;
  --footer:#0d0d0f;
  --white:#ffffff;
}
*{box-sizing:border-box;margin:0;padding:0}
html,body{width:1200px;height:3904px;overflow:hidden}
body{position:relative;background:var(--white);font-family:'Lato',sans-serif;color:var(--ink)}
.abs{position:absolute}
.btn{position:absolute;display:flex;align-items:center;justify-content:center;background:var(--cyan);color:var(--white);border-radius:20px;font-size:15px;height:39px}
.heading{font-family:'Michroma',sans-serif;font-size:27px;letter-spacing:3px;text-transform:uppercase;color:#1a1a1a;white-space:nowrap}
.heading b{color:var(--title-blue);font-weight:400}
.centered{left:0;width:1200px;text-align:center}
.wordmark{font-family:'Lato',sans-serif;font-weight:700;letter-spacing:8px;display:flex;align-items:center;gap:14px}
.wordmark i{display:block;border-radius:50%;background:var(--cyan)}

/* header */
.site-header{top:0;left:0;width:1200px;height:102px;background:var(--white)}
.site-header .wordmark{position:absolute;left:112px;top:30px;font-size:34px;color:#4a4a4a}
.site-header .wordmark i{width:40px;height:40px}
.nav a{position:absolute;top:40px;font-size:15px;color:#444;text-decoration:none}
.nav .active{top:36px;left:540px;width:67px;height:30px;border-radius:15px;background:var(--cyan);color:#fff;display:flex;align-items:center;justify-content:center}

/* hero */
.hero{top:102px;left:0;width:1200px;height:601px;background:linear-gradient(100deg,#0c2a3a 0%,#0f3a4c 45%,#0b2c3b 100%);clip-path:polygon(0 0,100% 0,100% 543px,1088px 601px,110px 601px,0 543px)}
.hero-visual{left:0;top:0;width:560px;height:601px;background:radial-gradient(ellipse at 40% 45%,#3fa4d6 0%,#1a5a7a 30%,#0e3447 65%,rgba(12,42,58,0) 100%)}
.hero h1{left:613px;top:128px;font-family:'Michroma',sans-serif;font-weight:400;font-size:40px;line-height:62px;letter-spacing:5px;color:#fff}
.hero p{left:613px;top:323px;font-size:23px;line-height:34px;color:#fff}

/* about */
.about-photo{left:112px;top:788px;width:453px;height:305px;background:linear-gradient(135deg,#8a8f94,#3e4248 55%,#6d6258);clip-path:polygon(0 0,50% 35px,100% 0,100% 100%,50% 270px,0 100%)}
.about-text{left:673px;top:865px;width:420px;font-size:14.5px;line-height:25.5px;color:var(--muted)}

/* industry */
.lead{font-size:16px;line-height:26px;color:#333}
.sector-title{font-family:'Michroma',sans-serif;font-size:16px;letter-spacing:3px;color:var(--title-blue);text-transform:uppercase;text-align:center;width:420px}
.sector-text{font-size:16px;line-height:26px;color:#444;text-align:center;width:420px}

/* why */
.why{top:1703px;left:0;width:1200px;height:400px;background:linear-gradient(180deg,#1f2a72 0%,#1f2a72 60%,#1c3f8a 85%,#1a5fa8 100%);clip-path:polygon(110px 0,1088px 0,1200px 57px,1200px 100%,0 100%,0 57px)}
.why-lights{left:0;top:300px;width:1200px;height:100px;background:linear-gradient(180deg,rgba(31,42,114,0),rgba(48,140,210,.55))}

/* blog */
.card-img{top:2268px;width:301px;height:232px}
.card-title{top:2524px;width:301px;text-align:center;font-size:23px;color:var(--title-blue)}
.card-text{top:2565px;width:301px;text-align:center;font-size:14.5px;line-height:23px;color:#555}
.arrow{top:2375px;width:30px;height:30px}

/* contact */
.field{background:var(--field);border-radius:3px;font-size:13px;color:#333;padding:18px 26px}

/* footer */
.footer{top:3334px;left:0;width:1200px;height:570px;background:var(--footer);clip-path:polygon(110px 0,1088px 0,1200px 56px,1200px 100%,0 100%,0 56px)}
.footer .wordmark{position:absolute;left:0;width:1200px;justify-content:center;top:92px;font-size:52px;color:#e8e8e8;letter-spacing:12px}
.footer .wordmark i{width:56px;height:56px}
.f-head{top:226px;font-size:21px;font-weight:700;color:#fff}
.f-list{top:272px;font-size:15px;line-height:38.5px;color:#fff;list-style:none}
.f-text{color:#fff;font-size:14.5px;line-height:26px}
.social{top:418px;width:30px;height:30px;border-radius:6px;background:#fff}
.copyright{top:547px;font-size:13px;color:#fff}
</style>
</head>
<body>

<header class="abs site-header">
  <div class="wordmark"><i></i>VORTEQ</div>
  <nav class="nav">
    <a class="active">Home</a>
    <a style="left:633px">About Us</a>
    <a style="left:735px">Products</a>
    <a style="left:834px">Contact Us</a>
  </nav>
  <span class="btn" style="left:935px;top:32px;width:153px">Get In Touch</span>
</header>

<section class="abs hero">
  <div class="abs hero-visual" role="img" aria-label="Hand holding a tablet with a glowing digital cloud network and connected service icons"></div>
  <h1 class="abs">INNOVATING<br>EVERYDAY<br>LIFE</h1>
  <p class="abs">Smarter, Sleeker, and More Efficient Solutions<br>for Everyday Life</p>
  <span class="btn" style="left:613px;top:428px;width:155px;height:38px">Get In Touch</span>
</section>

<section>
  <div class="abs about-photo" role="img" aria-label="Team of colleagues working together at a table with laptops"></div>
  <h2 class="abs heading" style="left:703px;top:800px">About <b>Us</b></h2>
  <p class="abs about-text">Lorem ipsum dolor sit amet, consectetur adipiscing elit, sed do eiusmod tempor incididunt ut labore et dolore magna aliqua. Ut enim ad minim veniam, quis nostrud exercitation ullamco laboris nisi ut aliquip ex ea commodo consequat. Duis aute irure dolor in reprehenderit in voluptate velit esse cillum dolore eu fugiat nulla pariatur.</p>
  <span class="btn" style="left:673px;top:1054px;width:154px">Read More</span>
</section>

<section>
  <h2 class="abs heading centered" style="top:1192px">Our <b>Industry</b></h2>
  <p class="abs lead centered" style="top:1248px">At Vorteq, we design smarter solutions for everyday living. From innovative<br>laundry accessories to next-generation pet treats, our products are<br>built for convenience, functionality, and modern lifestyles.</p>

  <svg class="abs" style="left:300px;top:1360px" width="86" height="90" viewBox="0 0 86 90" fill="none" stroke="#1b9cc8" stroke-width="3">
    <rect x="8" y="4" width="72" height="82" rx="4"/><line x1="8" y1="20" x2="80" y2="20"/>
    <circle cx="18" cy="12" r="2"/><line x1="40" y1="12" x2="70" y2="12"/>
    <circle cx="20" cy="56" r="17"/><circle cx="50" cy="58" r="15"/>
  </svg>
  <svg class="abs" style="left:800px;top:1355px" width="110" height="100" viewBox="0 0 110 100" fill="none" stroke="#1b9cc8" stroke-width="3">
    <circle cx="55" cy="22" r="18"/><circle cx="55" cy="22" r="7"/>
    <path d="M10 50a7 7 0 1 1 10-8l22 22a7 7 0 1 1-8 10L12 52z"/>
    <path d="M60 70l22-22a7 7 0 1 1 10 8L70 78a7 7 0 1 1-10-8z"/>
  </svg>

  <div class="abs sector-title" style="left:133px;top:1468px">Laundry Industry</div>
  <p class="abs sector-text" style="left:133px;top:1506px">Duis aute irure dolor in reprehenderit in voluptate<br>velit esse cillum dolore eu fugiat nulla pariatur.</p>
  <span class="btn" style="left:267px;top:1578px;width:153px">Read More</span>

  <div class="abs sector-title" style="left:647px;top:1468px">Pet Treats</div>
  <p class="abs sector-text" style="left:647px;top:1506px">Duis aute irure dolor in reprehenderit in voluptate<br>velit esse cillum dolore eu fugiat nulla pariatur.</p>
  <span class="btn" style="left:781px;top:1578px;width:153px">Read More</span>
</section>

<section class="abs why">
  <div class="abs why-lights" role="img" aria-label="Glowing blue city skyline lights"></div>
  <h2 class="abs heading centered" style="top:84px;color:#fff">Why Choose Vorteq?</h2>
  <p class="abs lead centered" style="top:155px;color:#fff;font-size:17px;line-height:27px">Smart, stylish, and functional—Vorteq creates innovative solutions that make everyday life easier.<br>From modern laundry accessories to revolutionary pet treats, our products are designed<br>for convenience, durability, and efficiency.</p>
  <span class="btn" style="left:477px;top:273px;width:246px;height:38px">Explore Our Innovations</span>
</section>

<section>
  <h2 class="abs heading centered" style="top:2202px">Our <b>Blog</b></h2>
  <svg class="abs arrow" style="left:59px" viewBox="0 0 30 30"><circle cx="15" cy="15" r="15" fill="#1b9cc8"/><path d="M17 9l-6 6 6 6" stroke="#fff" stroke-width="3" fill="none"/></svg>
  <svg class="abs arrow" style="left:1109px" viewBox="0 0 30 30"><circle cx="15" cy="15" r="15" fill="#1b9cc8"/><path d="M13 9l6 6-6 6" stroke="#fff" stroke-width="3" fill="none"/></svg>

  <div class="abs card-img" style="left:112px;background:linear-gradient(135deg,#5f7a8f,#2e3f4f)" role="img" aria-label="Colleagues gathered around a laptop"></div>
  <div class="abs card-img" style="left:449px;background:linear-gradient(135deg,#1d63b8,#0c2e6b)" role="img" aria-label="Hand tapping a digital checklist interface"></div>
  <div class="abs card-img" style="left:786px;background:linear-gradient(135deg,#2a5f9e,#0a1c40)" role="img" aria-label="Glowing blue data cubes"></div>

  <h3 class="abs card-title" style="left:112px">Lorem ipsum dolor sit</h3>
  <h3 class="abs card-title" style="left:449px">Lorem ipsum dolor sit</h3>
  <h3 class="abs card-title" style="left:786px">Lorem ipsum dolor sit</h3>
  <p class="abs card-text" style="left:112px">Excepteur sint occaecat cupidatat non proident, sunt in culpa qui officia dese-runt mollit anim id est laborum."</p>
  <p class="abs card-text" style="left:449px">Excepteur sint occaecat cupidatat non proident, sunt in culpa qui officia dese-runt mollit anim id est laborum."</p>
  <p class="abs card-text" style="left:786px">Excepteur sint occaecat cupidatat non proident, sunt in culpa qui officia dese-runt mollit anim id est laborum."</p>
  <span class="btn" style="left:185px;top:2653px;width:154px">Read More</span>
  <span class="btn" style="left:523px;top:2653px;width:154px">Read More</span>
  <span class="btn" style="left:860px;top:2653px;width:154px">Read More</span>
</section>

<section>
  <h2 class="abs heading centered" style="top:2792px">Contact <b>Us</b></h2>
  <p class="abs lead centered" style="top:2840px">Explore our comprehensive suite of data products, designed to give you<br>actionable insights and support your marketing strategies.</p>
  <div class="abs field" style="left:111px;top:2924px;width:480px;height:51px">First Name</div>
  <div class="abs field" style="left:608px;top:2924px;width:480px;height:51px">Last Name</div>
  <div class="abs field" style="left:111px;top:2994px;width:480px;height:51px">Phone</div>
  <div class="abs field" style="left:608px;top:2994px;width:480px;height:51px">Email</div>
  <div class="abs field" style="left:111px;top:3063px;width:977px;height:115px">Message</div>
  <span class="btn" style="left:523px;top:3209px;width:153px;height:38px">Submit</span>
</section>

<footer class="abs footer">
  <div class="wordmark"><i></i>VORTEQ</div>

  <h4 class="abs f-head" style="left:112px">About Us</h4>
  <p class="abs f-text" style="left:112px;top:278px;width:230px">Excepteur sint occaecat cupidatat non proident, sunt in culpa qui officia deserunt mollit anim id est laborum.</p>
  <span class="abs social" style="left:115px;background:#1b9cc8"></span>
  <span class="abs social" style="left:163px"></span>
  <span class="abs social" style="left:210px"></span>
  <span class="abs social" style="left:258px"></span>

  <h4 class="abs f-head" style="left:434px">Main Links</h4>
  <ul class="abs f-list" style="left:434px"><li>Home</li><li>About Us</li><li>Products</li><li>Industry</li><li>Contact Us</li></ul>

  <h4 class="abs f-head" style="left:650px">Contact Us</h4>
  <svg class="abs" style="left:651px;top:282px" width="18" height="22" viewBox="0 0 18 22" fill="none" stroke="#fff" stroke-width="1.6"><path d="M9 21s7-7 7-12A7 7 0 0 0 2 9c0 5 7 12 7 12z"/><circle cx="9" cy="9" r="2.5"/></svg>
  <p class="abs f-text" style="left:690px;top:278px;width:160px">45 Harbour Lane, Unit 7, Northfield 20418</p>
  <svg class="abs" style="left:651px;top:381px" width="18" height="18" viewBox="0 0 24 24" fill="none" stroke="#fff" stroke-width="1.8"><path d="M5 3h4l2 5-3 2a12 12 0 0 0 6 6l2-3 5 2v4a2 2 0 0 1-2 2A18 18 0 0 1 3 5a2 2 0 0 1 2-2z"/></svg>
  <p class="abs f-text" style="left:690px;top:380px">+ 1 555 010 2040</p>
  <svg class="abs" style="left:651px;top:432px" width="20" height="16" viewBox="0 0 20 16" fill="none" stroke="#fff" stroke-width="1.6"><rect x="1" y="1" width="18" height="14" rx="1"/><path d="M1 2l9 7 9-7"/></svg>
  <p class="abs f-text" style="left:690px;top:429px">hello@vorteq.example</p>

  <h4 class="abs f-head" style="left:955px">Other Links</h4>
  <ul class="abs f-list" style="left:955px"><li>Blog</li><li>Support</li><li>FAQs</li><li>Privacy Policy</li><li>Terms &amp; Conditions</li></ul>

  <div class="abs" style="left:112px;top:514px;width:976px;height:1px;background:#444"></div>
  <p class="abs copyright centered">Copyright © 2025 Vorteq . All rights reserved.</p>
</footer>

</body>
</html>
```